Poloshirt Packaging

We need a very attractive packaging design for our poloshirts. We are wholesaler of the schoolwear market. See what we currently have. I dont want any specific sizing put on the packaging. One design for all poloshirts (2 sides).
our logo is attached aswell

Target Market(s)

Parents

Requirements
Must have
• Our logo
Should not have
• size or age

```html
<!DOCTYPE html>
<html lang="en">
<head>
<meta charset="utf-8">
<title>Brightwell Poloshirt Packaging</title>
<link rel="stylesheet" href="https://fonts.googleapis.com/css2?family=Mulish:wght@400;600;700;800&display=swap">
<style>
  :root {
    --navy: #0f2f5f;
    --red: #d3262b;
    --mustard: #eeae2f;
    --mustard-light: #f3c35a;
    --wrap: #e8dcc0;
    --cyan: #17a3dc;
    --royal: #3444ae;
    --edge: #4a4a4a;
    --shadow: #c9c9c9;
    --white: #ffffff;
    --paper: #ffffff;
    --print-dark: #3a3020;
  }
  html, body {
    margin: 0;
    width: 1200px;
    height: 852px;
    overflow: hidden;
    background: var(--paper);
    font-family: "Mulish", sans-serif;
  }
  .stage {
    position: absolute;
    left: 0; top: 0;
    width: 1100px;
    height: 780px;
    transform: scale(1.0909, 1.0923);
    transform-origin: 0 0;
  }
  .pack-side {
    position: absolute;
    top: 18px;
    width: 526px;
    height: 742px;
    border: 1px solid var(--edge);
    box-shadow: 6px 6px 0 var(--shadow);
    overflow: hidden;
  }
  .pack-side--front { left: 14px; }
  .pack-side--back { left: 540px; width: 528px; }
  .shirt-photo {
    position: absolute;
    inset: 0;
    background:
      linear-gradient(180deg, var(--wrap) 0%, var(--mustard-light) 6%, var(--mustard) 30%, var(--mustard) 85%, #f0bf5d 100%);
  }
  .waves {
    position: absolute;
    inset: 0;
    width: 100%;
    height: 100%;
  }
  .brand-name {
    position: absolute;
    margin: 0;
    color: var(--navy);
    font-weight: 700;
    line-height: 1;
    letter-spacing: 0.5px;
    white-space: nowrap;
  }
  .product-name {
    position: absolute;
    margin: 0;
    color: var(--red);
    font-weight: 800;
    line-height: 1;
    letter-spacing: 1px;
    white-space: nowrap;
  }
  .pack-side--front .brand-name { left: 46px; top: 476px; font-size: 74px; }
  .pack-side--front .product-name { left: 48px; top: 554px; font-size: 34px; }
  .pack-side--back .brand-name { left: 108px; top: 218px; font-size: 58px; width: 312px; text-align: center; }
  .pack-side--back .product-name { left: 110px; top: 336px; font-size: 31px; width: 310px; text-align: center; }
  .feature-strip {
    position: absolute;
    left: 48px;
    top: 605px;
    margin: 0;
    padding: 3px 7px;
    background: var(--navy);
    color: var(--white);
    font-size: 10.5px;
    font-weight: 600;
    white-space: nowrap;
  }
  .safety-notice {
    position: absolute;
    left: 128px;
    top: 694px;
    width: 217px;
    height: 42px;
    margin: 0;
    border: 1px solid #5a4a30;
    color: var(--print-dark);
    font-size: 8px;
    font-weight: 700;
    line-height: 1.15;
    text-align: center;
    box-sizing: border-box;
    padding-top: 3px;
  }
  .safety-notice strong { display: block; text-decoration: underline; font-size: 9px; }
  .recycle-mark {
    position: absolute;
    left: 372px;
    top: 692px;
    width: 40px;
    height: 48px;
  }
</style>
</head>
<body>
<main class="stage">

  <section class="pack-side pack-side--front">
    <div class="shirt-photo" role="img" aria-label="Photograph of a folded mustard-yellow polo shirt, collar and placket visible, in a clear plastic wrapper"></div>
    <svg class="waves" viewBox="0 0 526 742" aria-hidden="true">
      <defs>
        <linearGradient id="wave-front" x1="0" x2="1" y1="0" y2="0">
          <stop offset="0" stop-color="var(--cyan)"/>
          <stop offset="1" stop-color="var(--royal)"/>
        </linearGradient>
        <linearGradient id="wave-front-corner" x1="0" x2="1" y1="1" y2="0">
          <stop offset="0" stop-color="var(--royal)"/>
          <stop offset="1" stop-color="#2a6fc4"/>
        </linearGradient>
      </defs>
      <path fill="url(#wave-front)" d="M0,352 C150,300 230,330 320,230 C400,150 470,140 526,172 L526,228 C470,210 420,232 370,292 C290,382 150,362 0,395 Z"/>
      <path fill="url(#wave-front-corner)" d="M310,742 C380,700 420,640 526,622 L526,664 C450,672 430,718 402,742 Z"/>
    </svg>
    <h1 class="brand-name">Brightwell</h1>
    <p class="product-name">POLOSHIRT</p>
    <p class="feature-strip">Superior weight fabric | Easy Care - Low iron | Reactive Dyes</p>
  </section>

  <section class="pack-side pack-side--back">
    <div class="shirt-photo" role="img" aria-label="Photograph of the back of a folded mustard-yellow polo shirt in a clear plastic wrapper"></div>
    <svg class="waves" viewBox="0 0 528 742" aria-hidden="true">
      <defs>
        <linearGradient id="wave-back" x1="0" x2="1" y1="0" y2="0">
          <stop offset="0" stop-color="var(--cyan)"/>
          <stop offset="1" stop-color="var(--royal)"/>
        </linearGradient>
        <linearGradient id="wave-back-corner" x1="0" x2="1" y1="1" y2="0">
          <stop offset="0" stop-color="var(--cyan)"/>
          <stop offset="1" stop-color="var(--royal)"/>
        </linearGradient>
      </defs>
      <path fill="url(#wave-back)" d="M0,374 C120,370 150,430 260,420 C360,410 420,370 528,385 L528,432 C430,440 380,500 250,497 C150,495 100,420 0,415 Z"/>
      <path fill="url(#wave-back-corner)" d="M365,742 C390,700 420,650 528,638 L528,690 C470,690 430,720 420,742 Z"/>
    </svg>
    <h2 class="brand-name">Brightwell</h2>
    <p class="product-name">POLOSHIRT</p>
    <p class="safety-notice"><strong>SAFETY FIRST</strong>TO AVOID DANGER OF SUFFOCATION KEEP THIS WRAPPER AWAY FROM BABIES AND CHILDREN</p>
    <svg class="recycle-mark" viewBox="0 0 40 48" role="img" aria-label="Recycling code 5, PP">
      <path d="M20,4 L37,34 L3,34 Z" fill="none" stroke="#3a3020" stroke-width="2.5" stroke-linejoin="round"/>
      <text x="20" y="29" font-size="12" font-weight="700" text-anchor="middle" fill="#3a3020" font-family="Mulish, sans-serif">5</text>
      <text x="20" y="45" font-size="8" font-weight="700" text-anchor="middle" fill="#3a3020" font-family="Mulish, sans-serif">PP</text>
    </svg>
  </section>

</main>
</body>
</html>
```